Governance Research Alumni Fellows' Association Annual Symposium Poster

We need a poster to advertise for our annual symposium. The poster will be printed on 11X17" paper.

Our organization is the Governance Research Alumni Fellows' Association. Our logo is in the uploaded files.

The title of this year's symposium is "Lakeside Currents - Paths Beyond Borders." The Symposium will take place on March 31, 2017 in HL - 41.

We are accepting papers on the topics of Canada and the world; Indigenous politics in Canada; Canadian national identity; Race, racialization and belonging; Gender and politics in Canada; Queer politics and sexualities; Class and labour politics in Canada; Environmental politics; Canadian government and politics.

There will be a lunch hour roundtable discussion on the topic of "Unweaving the Threads of Civic Inquiry."
Confirmed Speakers include Dr. Rosalind Okafor, Dr. Teresa Valdomero-Cuesta, Dr. Owen Tillard, Dr. Harriet Brisco
This round-table will consider questions of Race, Indigeneity, and Ethnicity in Political Science Research and efforts by the universities to "Decolonize," "Indigenize," and "Reconcile" the academy.
The roundtable will take place in HL-41 from 12:00 - 1:00 pm.
Lunch will be provided.

There will be a keynote panel sponsored by the Northern Institute for Civilian Safeguard Studies on the topic of "Canada’s renewed vision of peacekeeping."
Their logo is in the uploaded files.

For more information and a full schedule or events, visit our website: http://grafaforum.quillpage.example/credits.html

Sponsors should be listed at the bottom of the page: The Faculty of Arts, The Department of Political Science, NICSS

Target Market(s)

University students and staff who may come to the symposium

Industry/Entity Type

Political

Logo Text

GRAFA Governance Research Alumni Fellows' Association

Font styles to use
Sans Serif

Colors
ec1f27
f37122
9bcb3c
ffcf3e

Requirements
Must have
• Coulours/Leaves/etc should match this website:
• http://grafaforum.quillpage.example/credits.html
• Title of Symposium, Date, Room Number
• Sponsor logos at the bottom of the page
• Date/Time for Roundtable
Nice to have
• This list:
• We are accepting papers on the topics of Canada and the world; Indigenous politics in Canada; Canadian national identity; Race, racialization and belonging; Gender and politics in Canada; Queer politics and sexualities; Class and labour politics in Canada; Environmental politics; Canadian government and politics.
• This statement:
• This round-table will consider questions of Race, Indigeneity, and Ethnicity in Political Science Research and efforts by the universities to "Decolonize," "Indigenize," and "Reconcile" the academy.

```html
<!DOCTYPE html>
<html lang="en">
<head>
<meta charset="utf-8">
<title>Lakeside Currents: Paths Beyond Borders — Symposium Poster</title>
<link href="https://fonts.googleapis.com/css2?family=Ubuntu:wght@400;500&family=Ubuntu+Condensed&family=Oswald:wght@300;400&display=swap" rel="stylesheet">
<style>
  :root {
    --red: #ec1f27;
    --orange: #f37122;
    --green: #9bcb3c;
    --yellow: #ffcf3e;
    --header: #3a3a3c;
    --column: #231f20;
    --paper: #f1e6dd;
    --ink: #231f20;
    --white: #ffffff;
    --footer-ink: #2a2a2a;
    --condensed: "Ubuntu Condensed", "Oswald", "Arial Narrow", sans-serif;
  }
  * { box-sizing: border-box; margin: 0; padding: 0; }
  html, body { width: 1200px; height: 1200px; overflow: hidden; background: var(--white); }
  body { font-family: "Ubuntu", sans-serif; color: var(--ink); }

  .poster {
    position: absolute; left: 246px; top: 54px;
    width: 678px; height: 1046px;
    background: var(--paper); overflow: hidden;
  }
  .poster > * { position: absolute; }

  .header { left: 0; top: 0; width: 678px; height: 168px; background: var(--header); overflow: hidden; }
  .header-rule { position: absolute; left: 0; top: 24px; width: 429px; height: 5px; background: var(--red); }
  .leaves-autumn {
    position: absolute; left: 452px; top: 0; width: 226px; height: 126px;
    background: radial-gradient(ellipse at 30% 45%, var(--red) 0 38%, transparent 39%),
                radial-gradient(ellipse at 75% 45%, var(--yellow) 0 40%, transparent 41%);
  }
  .title {
    position: absolute; left: 19px; top: 40px; width: 650px;
    font-family: var(--condensed); font-weight: 400;
    color: var(--white); font-size: 56px; line-height: 62px;
    text-transform: uppercase; white-space: nowrap;
  }
  .title span { display: block; }

  .leaf-spring {
    left: 540px; top: 180px; width: 134px; height: 136px;
    background: radial-gradient(ellipse at 50% 45%, #8cc63f 0 45%, transparent 46%);
  }

  .column { left: 0; top: 168px; width: 245px; height: 782px; background: var(--column); }
  .band-rule { left: 245px; top: 168px; width: 433px; height: 5px; background: var(--red); }

  .label {
    left: 0; width: 282px; height: 52px; background: var(--orange);
    font-family: var(--condensed); font-weight: 400; color: var(--white);
    font-size: 24px; line-height: 52px; padding-left: 16px; text-transform: uppercase;
    white-space: nowrap; overflow: hidden;
  }
  .fold { left: 245px; width: 37px; height: 16px; }
  .fold svg { display: block; }

  .detail { left: 303px; font-weight: 500; font-size: 21px; line-height: 24px; text-transform: uppercase; white-space: nowrap; }
  .green-rule { height: 3px; background: var(--green); }

  .side-text { left: 15px; width: 215px; color: var(--white); }
  .speakers { font-family: var(--condensed); font-size: 14px; line-height: 18.5px; text-transform: uppercase; white-space: nowrap; }
  .speakers ul { list-style: none; margin-top: 18px; }

  .proposal { font-size: 13.4px; line-height: 17.4px; text-align: justify; }
  .proposal h3 { font-weight: 400; font-size: 14.5px; margin-bottom: 8px; }

  .blurb { left: 322px; width: 318px; font-size: 14.4px; line-height: 18.4px; text-align: justify; }
  .call-lead { left: 303px; width: 346px; font-weight: 500; font-size: 20.5px; line-height: 25px; text-align: justify; }
  .topics { left: 322px; width: 328px; list-style: none; font-size: 14.4px; line-height: 22.4px; }
  .topics li { position: relative; }
  .topics li::before {
    content: ""; position: absolute; left: -15px; top: 7px;
    width: 8px; height: 8px; border-radius: 50%; background: var(--ink);
  }
  .sponsor-lead { left: 303px; width: 346px; font-weight: 500; font-size: 20.5px; line-height: 25px; }
  .sponsor-topic { left: 322px; width: 288px; font-size: 14.4px; line-height: 18.4px; }

  .rule-red { left: 245px; top: 937px; width: 433px; height: 5px; background: var(--red); }
  .rule-black { left: 0; top: 945px; width: 678px; height: 6px; background: var(--column); }

  .footer { left: 0; top: 951px; width: 678px; height: 95px; display: flex; align-items: center; }
  .sponsor {
    flex: 1; display: flex; align-items: center; justify-content: center; gap: 8px;
    color: var(--footer-ink); font-weight: 500; font-size: 13px; line-height: 16px; text-align: center;
  }
  .sponsor + .sponsor { border-left: 1.5px solid var(--footer-ink); height: 62px; }
  .sponsor-name-lg { font-size: 28px; line-height: 30px; }
  .sponsor-mark { width: 14px; height: 14px; background: var(--footer-ink); }
  .sponsor-dot { width: 14px; height: 14px; border-radius: 50%; background: var(--footer-ink); }
</style>
</head>
<body>
<main class="poster">
  <header class="header">
    <div class="header-rule"></div>
    <div class="leaves-autumn" role="img" aria-label="Red and yellow maple leaf illustration"></div>
    <h1 class="title"><span>Lakeside Currents:</span><span>Paths Beyond Borders</span></h1>
  </header>

  <div class="column"></div>
  <div class="band-rule"></div>

  <div class="label" style="top:178px">Date of Symposium</div>
  <div class="fold" style="top:230px"><svg width="37" height="16"><polygon points="0,0 37,0 0,16" fill="#ec1f27"/></svg></div>
  <div class="label" style="top:254px">Room Number</div>
  <div class="fold" style="top:306px"><svg width="37" height="16"><polygon points="0,0 37,0 0,16" fill="#ec1f27"/></svg></div>
  <div class="label" style="top:330px">Lunchtime Roundtable</div>
  <div class="fold" style="top:382px"><svg width="37" height="16"><polygon points="0,0 37,0 0,16" fill="#ec1f27"/></svg></div>
  <div class="label" style="top:546px">Call for Papers</div>
  <div class="fold" style="top:598px"><svg width="37" height="16"><polygon points="0,0 37,0 0,16" fill="#ec1f27"/></svg></div>
  <div class="label" style="top:835px">Keynote Panel</div>
  <div class="fold" style="top:887px"><svg width="37" height="16"><polygon points="0,0 37,0 0,16" fill="#ec1f27"/></svg></div>

  <p class="detail" style="top:199px">March 31, 2017</p>
  <div class="green-rule" style="left:294px;top:249px;width:260px"></div>
  <p class="detail" style="top:271px">HL - 41</p>
  <div class="green-rule" style="left:294px;top:307px;width:260px"></div>
  <div class="leaf-spring" role="img" aria-label="Green maple leaf illustration"></div>

  <p class="detail" style="top:334px">Friday, March 31st, 2017<br>12:00 - 1:00 PM</p>
  <p class="blurb" style="top:397px">This round-table will consider questions of Race, Indigeneity, and Ethnicity in Political Science Research and efforts by the universities to "Decolonize," "Indigenize," and "Reconcile" the academy.</p>

  <div class="side-text speakers" style="top:399px">
    <p>Confirmed speakers:</p>
    <ul>
      <li>Dr. Rosalind Okafor</li>
      <li>Dr. Teresa Valdomero-Cuesta</li>
      <li>Dr. Owen Tillard</li>
      <li>Dr. Harriet Brisco</li>
    </ul>
  </div>

  <div class="green-rule" style="left:294px;top:525px;width:355px"></div>
  <p class="call-lead" style="top:548px">We are accepting papers on the topics of Canada and the world.</p>
  <ul class="topics" style="top:603px">
    <li>Indigenous Politics in Canada</li>
    <li>Canadian National Identity</li>
    <li>Race</li>
    <li>Racialization and Belonging</li>
    <li>Gender and Politics in Canada</li>
    <li>Queer Politics and Sexualities</li>
    <li>Class and Labour Politics in Canada</li>
    <li>Environmental politics</li>
    <li>Canadian Government and Politics.</li>
  </ul>

  <div class="side-text proposal" style="top:617px">
    <h3>Deadline for Proposals</h3>
    <p>By February 1st, authors should submit brief proposal for their papers including the title and a short description of the topic(s) to be addressed. Proposals can be submitted via e-mail to the GRAFA by emailing Corinne at cdvarnel@northvale.example</p>
  </div>

  <div class="green-rule" style="left:294px;top:817px;width:355px"></div>
  <p class="sponsor-lead" style="top:838px">Sponsored by the Northern Institute for Civilian Safeguard Studies</p>
  <p class="sponsor-topic" style="top:893px">Topic: Canada’s renewed vision of peacekeeping</p>

  <div class="rule-red"></div>
  <div class="rule-black"></div>

  <footer class="footer">
    <div class="sponsor"><span class="sponsor-mark"></span><span>Northvale University<br>Faculty of Arts<br>Department of Political Science</span></div>
    <div class="sponsor"><span class="sponsor-name-lg">GRAFA</span></div>
    <div class="sponsor"><span class="sponsor-name-lg">NICSS</span><span class="sponsor-dot"></span></div>
  </footer>
</main>
</body>
</html>
```